Velmori Sciences needs high end Label Design for a revolutionary new supplement

We at Velmori Sciences are looking for a brand new Label Design for a first of its kind product called Solvenna. It is the first supplement on the market that treats grief and heartbreak. This product is unisex for both men and woman. We want the New Label to look high end and luxurious using the brand colors which are gold and burgundy. Please feel free to use other colors such as black, white, or gray to go along with it or any other colors if you feel would be a great fit! Velmori Sciences is like the Tarnwick of the supplement world, coming out with new products that will challenge the way people treat different symptoms. To Recap:

1. Product Name: SOLVENNA - the font will play a big roll
2. The Label will be placed on an all white bottle
3. Some parts of the label will be printed with foil to make parts of the label shiny and more attractive. Please keep this in mind when designing.
4. Must use our Logo. I will attach a file of our logo and of the emblem as well. Feel free to use the emblem separately if you have a great idea for it. Please let us know if you need the Logo in a different file type.
5. This all natural herbal supplement in pill form is the first to treat grief and support someone with a broken heart. The consumers purchasing this product will be going through a hard and emotional time. This is a serious product.
6. The manufacturer has included some basic instructions regarding the dye line and file types. Please do your best to meet these. If you cannot meet the guidelines please submit art work anyways. If your design is chosen we will just have the manufacturer replicate the design.

The final label should portray Solvenna and Velmori Sciences as a luxurious brand and product which was made with cutting edge science leading the way with revolutionary ideas. We want customers to feel that the product is worth every penny, because it is. As soon as they receive the product and take one look at the label, I want them to think WOW I made the right choice buying this. I have attached some Label designs that we really liked for your review.

Please feel free to message me with any questions or if you need the Logo in a different file type. Thank you all.
Updates

Please send in more entries while we take a couple days to review, we are still looking for that one design we can work with. We are getting close, thank you all!

Target Market(s)

People going through grief and heartbreak.

Font styles to use
Sans Serif
Script
Other font styles liked:
• Any font that looks good, The font for the name SOLVENNA is very important and will brand it. We hated the font used in the label we received in our first label draft (attached so you can see)

Requirements
Must have
• Must have the company Logo that says the company name
• Must have the colors Gold and Burgundy
• Must have some areas that will be the shiny foil when label is printed.
• Must say "Dietary Supplement" somewhere near the bottom along with "90 Capsules"
• I have attached a Label someone designed for us but were not really happy with. I did like the font the "Dietary supplement" and "90 Capsules" had and also where it was placed. We absolutely HATED the font used for Solvenna.
• Must look at the label design we received from the manufacturer and take into consideration the room needed to write in the directions and all the symbols such as "made in america" and "KMT Facility" Don't worry about adding these in as they will put those in before printing but keep in mind they will be added to the Final Label along with the Supplement Facts.
Nice to have
• Would like to see other colors to go with gold and burgundy suck as black, white, or gray. I have attached some Label designs that I really liked for your reference.
Should not have
• Does not need to have any other legal language, that will be applied by the the manufacturer's graphics team.

```html
<!DOCTYPE html>
<html lang="en">
<head>
<meta charset="utf-8">
<title>Solvenna – Dietary Supplement Label</title>
<link rel="stylesheet" href="https://fonts.googleapis.com/css2?family=Josefin+Sans:wght@300;400;700&family=Montserrat:wght@400;500;700&display=swap">
<style>
  :root {
    --backdrop: #efefef;
    --burgundy-deep: #2a1117;
    --burgundy: #4a1c27;
    --burgundy-light: #5e2533;
    --band: #1a1718;
    --band-edge: #111010;
    --gold-light: #f3d29a;
    --gold: #c9954f;
    --gold-deep: #8a5a2b;
    --ink-light: #f4f2f0;
    --ink-muted: #d8cfcb;
  }
  html, body {
    margin: 0;
    width: 1200px;
    height: 1200px;
    overflow: hidden;
    background: var(--backdrop);
  }
  .canvas {
    position: relative;
    width: 1200px;
    height: 1200px;
  }
  .label {
    position: absolute;
    left: 80px;
    top: 100px;
    width: 1040px;
    height: 1000px;
    overflow: hidden;
    background: var(--burgundy-deep);
  }
  .label__pattern {
    position: absolute;
    inset: 0;
    background: radial-gradient(circle at 50% 50%, var(--burgundy-light) 0%, var(--burgundy) 40%, var(--burgundy-deep) 100%);
  }
  .brand {
    position: absolute;
    top: 70px;
    left: 0;
    right: 0;
    display: flex;
    justify-content: center;
    align-items: center;
    gap: 16px;
    margin: 0;
    font-family: "Montserrat", sans-serif;
    font-weight: 500;
    font-size: 26px;
    letter-spacing: 0.28em;
    color: var(--gold);
  }
  .brand__mark {
    width: 18px;
    height: 18px;
    border-radius: 50%;
    background: var(--gold);
  }
  .name-band {
    position: absolute;
    left: 0;
    top: 380px;
    width: 1040px;
    height: 260px;
    background: linear-gradient(180deg, var(--band-edge) 0%, var(--band) 50%, var(--band-edge) 100%);
  }
  .name-band__rules,
  .name-band__seal {
    position: absolute;
    left: 0;
    top: 0;
  }
  .name-band__seal {
    top: -40px;
  }
  .product-name {
    position: absolute;
    left: 0;
    right: 0;
    top: 78px;
    margin: 0;
    text-align: center;
    font-family: "Josefin Sans", sans-serif;
    font-weight: 300;
    font-size: 104px;
    line-height: 1;
    letter-spacing: 0.06em;
    color: var(--ink-light);
  }
  .label__category {
    position: absolute;
    bottom: 118px;
    left: 0;
    right: 0;
    margin: 0;
    text-align: center;
    font-family: "Montserrat", sans-serif;
    font-weight: 500;
    font-size: 21px;
    letter-spacing: 0.32em;
    color: var(--ink-muted);
  }
  .label__count {
    position: absolute;
    bottom: 36px;
    left: 0;
    right: 0;
    margin: 0;
    text-align: center;
    font-family: "Montserrat", sans-serif;
    color: var(--ink-light);
  }
  .label__count-number {
    font-weight: 700;
    font-size: 44px;
    letter-spacing: 0.04em;
  }
  .label__count-unit {
    font-weight: 700;
    font-size: 17px;
    letter-spacing: 0.08em;
    margin-left: 8px;
  }
</style>
</head>
<body>
<main class="canvas">
  <section class="label">
    <div class="label__pattern" role="img" aria-label="Burgundy mandala ornament pattern covering the label"></div>

    <p class="brand"><span class="brand__mark"></span>VELMORI SCIENCES</p>

    <div class="name-band">
      <svg class="name-band__rules" width="1040" height="260" viewBox="0 0 1040 260" aria-hidden="true">
        <defs>
          <pattern id="goldDots" x="0" y="0" width="12" height="8" patternUnits="userSpaceOnUse">
            <circle cx="6" cy="4" r="2" fill="#c9954f"/>
          </pattern>
        </defs>
        <rect x="0" y="18" width="1040" height="8" fill="url(#goldDots)"/>
        <rect x="0" y="234" width="1040" height="8" fill="url(#goldDots)"/>
      </svg>

      <svg class="name-band__seal" width="1040" height="340" viewBox="0 0 1040 340" aria-hidden="true">
        <defs>
          <linearGradient id="ringGold" x1="0" y1="0" x2="1" y2="1">
            <stop offset="0" stop-color="#f3d29a"/>
            <stop offset="0.35" stop-color="#c9954f"/>
            <stop offset="0.6" stop-color="#8a5a2b"/>
            <stop offset="1" stop-color="#e8bd7c"/>
          </linearGradient>
        </defs>
        <circle cx="520" cy="170" r="164" fill="#121112" stroke="url(#ringGold)" stroke-width="7"/>
        <circle cx="520" cy="170" r="152" fill="none" stroke="#c9954f" stroke-opacity="0.35" stroke-width="1.5"/>
      </svg>

      <h1 class="product-name">SOLVENNA</h1>
    </div>

    <p class="label__category">DIETARY SUPPLEMENT</p>

    <p class="label__count">
      <span class="label__count-number">90</span><span class="label__count-unit">CAPSULES</span>
    </p>
  </section>
</main>
</body>
</html>
```